Website design for Puddle Jump Kidscare

I need a website designed for my daycare business, Puddle Jump Kidscare, now that I have a new logo. My former website was ok but simple and I did not have a logo yet. It also was created by me using a template and was entirely pink. I loved the bright, happy feel of it but worried it might not appeal as much to potential clients who have sons. Therefore, I need a site which will appeal to both genders while still keeping the cheerful color scheme of my new logo, which has pinks, blue, green and cream.
Updates

Reason: Hello! I am still trying to download my new logo and am sorry it is taking me so long. Hopefully I will it posted by the end of today (US Eastern Standard Time). Thank you all very much for your patience!

Hello! I have finally managed to upload my new logo for you to use in designing my website. I'm sorry it took so long and greatly appreciate your time and creative efforts! I look forward to seeing what is submitted based on my logo design and its style/colors.

Many thanks!

Reason: As I've been traveling and posted my logo file late, I am extending my deadline. I am now back and can focus on providing more and better feedback. I appreciate your patience and submissions very much!

Reason: I need more time to provide feedback and make decisions.

Industry/Entity Type

Daycare

Colors
0192cd
33a6d7
86cae7
cadf82
fbf289
add136
e34197

```html
<!DOCTYPE html>
<html lang="en">
<head>
<meta charset="utf-8">
<title>Puddle Jump Kidscare</title>
<link href="https://fonts.googleapis.com/css2?family=Signika:wght@400;600;700&display=swap" rel="stylesheet">
<style>
  :root {
    --white: #ffffff;
    --sky: #74b4da;
    --sky-strip: #7ab9d8;
    --blush: #fcb9bb;
    --leaf: #98d19d;
    --leaf-strip: #9dd09f;
    --coral: #fc7e80;
    --coral-strip: #f47c7c;
    --blush-strip: #f9b5b7;
    --link: #f47a7a;
    --link-active: #8fcf94;
    --social-blue: #3e5f9a;
    --social-orange: #f08a2c;
  }
  * { box-sizing: border-box; margin: 0; padding: 0; }
  html, body { width: 1200px; height: 961px; overflow: hidden; }
  body {
    position: relative;
    font-family: "Signika", sans-serif;
    background: var(--white);
  }
  .backdrop {
    position: absolute; inset: 0;
    background:
      linear-gradient(125deg, #f7a3a5 0%, #fbd3cf 18%, #fde9a8 35%, #a9d3ea 52%, #f6b4b4 68%, #9fd3a3 84%, #f7e7a0 100%);
  }
  .main-nav {
    position: absolute; left: 497px; top: 102px; width: 565px; height: 32px;
    background: var(--white);
    display: flex; align-items: center;
    padding-left: 19px;
  }
  .main-nav a {
    font-size: 14px; color: var(--link); text-decoration: none;
    margin-right: 38px;
  }
  .main-nav a.is-current { color: var(--link-active); }
  .main-nav a:last-child { margin-right: 0; }
  .page-frame {
    position: absolute; left: 174px; top: 149px; width: 887px; height: 736px;
    background: var(--white);
  }
  .hero-photo {
    position: absolute; left: 194px; top: 166px; width: 845px; height: 520px;
    background: linear-gradient(160deg, #a9a2bb 0%, #c0aab0 40%, #d7b9a0 65%, #7aa7d6 100%);
  }
  .info-card {
    position: absolute; top: 698px; width: 203px; height: 168px;
    color: var(--white);
    border-top: 7px solid;
    padding: 15px 13px 0;
  }
  .info-card h2 { font-size: 21px; font-weight: 700; line-height: 1; margin-bottom: 7px; }
  .info-card p { font-size: 12px; line-height: 14.5px; font-weight: 600; }
  .info-card p.lead { font-size: 13px; line-height: 16px; font-weight: 400; }
  .info-card strong { font-weight: 700; }
  .card-button {
    position: absolute; left: 11px; right: 11px; bottom: 11px; height: 19px;
    background: var(--white); color: var(--link);
    font-size: 13px; text-align: right; padding-right: 10px; line-height: 19px;
    text-decoration: none;
  }
  .card-about { left: 193px; background: var(--sky); border-color: var(--leaf-strip); }
  .card-programs { left: 408px; background: var(--blush); border-color: var(--sky-strip); }
  .card-staff { left: 622px; background: var(--leaf); border-color: var(--coral-strip); }
  .card-contact { left: 837px; background: var(--coral); border-color: var(--blush-strip); }
  .social-links { position: absolute; left: 1010px; top: 915px; display: flex; gap: 5px; }
  .social-links span { width: 24px; height: 24px; border-radius: 4px; display: block; }
  .social-links .social-one { background: var(--social-blue); }
  .social-links .social-two { background: var(--social-orange); }
</style>
</head>
<body>
  <div class="backdrop" role="img" aria-label="Pastel background of large overlapping coloured shapes"></div>

  <nav class="main-nav">
    <a href="#" class="is-current">Home</a>
    <a href="#">About Us</a>
    <a href="#">Programs</a>
    <a href="#">Staff</a>
    <a href="#">News &amp; Events</a>
    <a href="#">Contact</a>
  </nav>

  <div class="page-frame"></div>
  <div class="hero-photo" role="img" aria-label="Photo of a toddler playing with wooden shape blocks at a classroom table"></div>

  <section class="info-card card-about">
    <h2>About us</h2>
    <p>I'm a paragraph. Click here to add your own text and edit me. I'm a great place for you to tell a story and let your users know a little more about you.</p>
    <a class="card-button" href="#">Read more</a>
  </section>

  <section class="info-card card-programs">
    <h2>Programs</h2>
    <p>I'm a paragraph. Click here to add your own text and edit me. I'm a great place for you to tell a story and let your users know a little more about you.</p>
    <a class="card-button" href="#">More Details</a>
  </section>

  <section class="info-card card-staff">
    <h2>Meet our staff</h2>
    <p>I'm a paragraph. Click here to add your own text and edit me. I'm a great place for you to tell a story and let your users know a little more about you.</p>
    <a class="card-button" href="#">Read more</a>
  </section>

  <section class="info-card card-contact">
    <h2>Contact us</h2>
    <p class="lead">We are now accepting registrations for <strong>September 2022</strong></p>
    <a class="card-button" href="#">Contact us</a>
  </section>

  <div class="social-links" aria-label="Social links">
    <span class="social-one"></span>
    <span class="social-two"></span>
  </div>
</body>
</html>
```